Gift Cards in the Mail Envelope

Mailing out gift cards in the envelope. Need an eye popping envelope. Please look at the enclosed images. The envelope should look like that.

Low design quality

```html
<!DOCTYPE html>
<html lang="en">
<head>
<meta charset="utf-8">
<title>Gift Card – Virtual Gift Voucher</title>
<link rel="stylesheet" href="https://fonts.googleapis.com/css2?family=Fredoka:wght@500;600&family=Montserrat:ital,wght@0,500;0,700;1,500&display=swap">
<style>
  :root {
    --backdrop: #d9d9d9;
    --paper: #ffffff;
    --sunflower: #fbd314;
    --ink: #222222;
  }
  * { margin: 0; padding: 0; box-sizing: border-box; }
  html, body {
    width: 1200px;
    height: 1200px;
    overflow: hidden;
    background: var(--backdrop);
  }
  .sheet {
    position: relative;
    width: 1200px;
    height: 1200px;
  }
  .card {
    position: absolute;
    left: 277px;
    width: 647px;
    height: 431px;
    background: var(--paper);
    overflow: hidden;
  }
  .card--front { top: 154px; }
  .card--back { top: 616px; }

  .ribbon-art {
    position: absolute;
    left: 300px;
    top: 0;
    width: 347px;
    height: 431px;
  }

  .headline {
    position: absolute;
    left: 32px;
    top: 108px;
    font-family: "Fredoka", sans-serif;
    font-weight: 600;
    line-height: 0.86;
    letter-spacing: -2px;
  }
  .headline__gift { display: block; color: var(--sunflower); font-size: 128px; }
  .headline__card { display: block; color: var(--ink); font-size: 128px; }

  .voucher-note {
    position: absolute;
    left: 34px;
    top: 370px;
    font-family: "Montserrat", sans-serif;
  }
  .voucher-note__label {
    color: var(--sunflower);
    font-weight: 700;
    font-size: 12.5px;
    letter-spacing: 0.2px;
  }
  .voucher-note__text {
    color: var(--ink);
    font-weight: 500;
    font-size: 13px;
    margin-top: 2px;
  }

  .open-me {
    position: absolute;
    left: 0;
    right: 0;
    top: 130px;
    text-align: center;
    font-family: "Fredoka", sans-serif;
    font-weight: 600;
    font-size: 27px;
    letter-spacing: -0.5px;
  }
  .open-me__open { color: var(--sunflower); }
  .open-me__me { color: var(--ink); }

  .footnote {
    position: absolute;
    left: 0;
    right: 0;
    top: 389px;
    text-align: center;
    font-family: "Montserrat", sans-serif;
    font-style: italic;
    font-weight: 500;
    font-size: 9.5px;
    color: var(--ink);
  }
</style>
</head>
<body>
<main class="sheet">
  <section class="card card--front">
    <svg class="ribbon-art" role="img" aria-label="Hand-drawn yellow ribbon tied in a bow across the card, with yellow paint splashes" viewBox="0 0 347 431">
      <defs>
        <radialGradient id="ribbonGlow" cx="0.62" cy="0.45" r="0.7">
          <stop offset="0" stop-color="#fbd314"/>
          <stop offset="0.55" stop-color="#fce35f"/>
          <stop offset="1" stop-color="#ffffff"/>
        </radialGradient>
      </defs>
      <rect width="347" height="431" fill="url(#ribbonGlow)"/>
    </svg>

    <h1 class="headline">
      <span class="headline__gift">Gift</span>
      <span class="headline__card">Card</span>
    </h1>

    <div class="voucher-note">
      <p class="voucher-note__label">VIRTUAL GIFT VOUCHER</p>
      <p class="voucher-note__text">You have received a Gift Card from us.</p>
    </div>
  </section>

  <section class="card card--back">
    <p class="open-me"><span class="open-me__open">Open</span> <span class="open-me__me">Me</span></p>
    <p class="footnote">* More information on our website: (website address)</p>
  </section>
</main>
</body>
</html>
```